Brindle Yard Care. The best in the biz

I run a lawn care service that offers full service mowing. 100% satisfaction guarantee. Fast, Friendly, quality service "I am your lawns best friend" I cut residential lawns. I offer a mow package that includes trimming, edging and clean up. Prices very from 20 dollars to 75. I want my logo to stand out. Free estimates

Target Market(s)

Home owners

Industry/Entity Type

Landscaping

Contact Information for Business Card

555-812-4473 tomvale48@quillmail.net Derek. Brindle Yard care

Colors
f37122
9bcb3c
cadf82

Requirements
Must have
• Company name.
• Phone number
• Email
• My services
• images
Nice to have
• A sun that is growing grass.
Should not have
• Incorrect information

```html
<!DOCTYPE html>
<html lang="en">
<head>
<meta charset="utf-8">
<title>Brindle Yard Care – Business Card</title>
<link rel="stylesheet" href="https://fonts.googleapis.com/css2?family=Source+Sans+3:wght@400;600&display=swap">
<style>
  :root {
    --card-bg: #ffffff;
    --brand-green: #169b48;
    --sun-yellow: #f5d00f;
    --text-grey: #6d6e70;
    --divider-grey: #a7a9ac;
  }
  * { margin: 0; padding: 0; box-sizing: border-box; }
  html, body {
    width: 1200px;
    height: 704px;
    overflow: hidden;
    background: var(--card-bg);
  }
  .card {
    position: relative;
    width: 1200px;
    height: 704px;
    background: var(--card-bg);
    font-family: "Source Sans 3", "Myriad Pro", Arial, sans-serif;
  }
  .brand {
    position: absolute;
    left: 40px;
    top: 300px;
    width: 480px;
    display: flex;
    align-items: center;
    justify-content: center;
    gap: 16px;
  }
  .brand-dot {
    width: 52px;
    height: 52px;
    border-radius: 50%;
    background: var(--sun-yellow);
    flex: none;
  }
  .brand-name {
    font-size: 36px;
    font-weight: 600;
    color: var(--brand-green);
    white-space: nowrap;
  }
  .divider {
    position: absolute;
    left: 539px;
    top: 133px;
    width: 1px;
    height: 412px;
    background: var(--divider-grey);
  }
  .contact {
    position: absolute;
    left: 611px;
    top: 206px;
  }
  .contact-name {
    font-size: 50px;
    font-weight: 600;
    color: var(--brand-green);
    line-height: 1;
    margin-bottom: 58px;
  }
  .contact-row {
    display: flex;
    align-items: center;
    gap: 14px;
    font-size: 42px;
    font-weight: 400;
    color: var(--text-grey);
    line-height: 1;
    height: 52px;
  }
  .contact-icon {
    width: 32px;
    height: 32px;
    flex: none;
    fill: var(--sun-yellow);
  }
  .tagline {
    position: absolute;
    left: 0;
    top: 582px;
    width: 1200px;
    text-align: center;
    font-size: 46px;
    font-weight: 600;
    color: var(--brand-green);
    line-height: 1;
  }
</style>
</head>
<body>
  <main class="card">
    <div class="brand">
      <span class="brand-dot"></span>
      <span class="brand-name">Brindle Yard Care</span>
    </div>

    <div class="divider"></div>

    <section class="contact">
      <p class="contact-name">Derek</p>
      <p class="contact-row">
        <svg class="contact-icon" viewBox="0 0 24 24" aria-hidden="true">
          <path d="M6.6 10.8a15.1 15.1 0 0 0 6.6 6.6l2.2-2.2c.3-.3.7-.4 1-.2 1.1.4 2.3.6 3.6.6.6 0 1 .4 1 1V20c0 .6-.4 1-1 1A17 17 0 0 1 3 4c0-.6.4-1 1-1h3.5c.6 0 1 .4 1 1 0 1.3.2 2.5.6 3.6.1.3 0 .7-.2 1z"/>
        </svg>
        <span>555-812-4473</span>
      </p>
      <p class="contact-row">
        <svg class="contact-icon" viewBox="0 0 24 24" aria-hidden="true">
          <path d="M2 5h20v14H2z"/>
          <path d="M2 5l10 8 10-8" fill="none" stroke="#ffffff" stroke-width="1.6"/>
        </svg>
        <span>tomvale48@quillmail.net</span>
      </p>
    </section>

    <p class="tagline">I am your lawns best friend</p>
  </main>
</body>
</html>
```